Small Business Broker Business Card Design

A business card design for a small business brokerage, which is a financial service, not unlike real estate brokerage, but for small businesses such as laundromats, pizza shops, restaurants, cleaners etc. The designs should all be simple, more conservative in nature, using the colors and font of the logo. Again, think real estate Brokerage as a business context
Contact Information for Business Card
Name: Glen R. Harlow. Title: Small Business Advisor. Email: g.harlow@bayfieldcapitalworks.example. Mobile: (555) 274-3918. Office: (555) 806-2147. www.bayfieldcapitalworks.example

```html
<!DOCTYPE html>
<html lang="en">
<head>
<meta charset="utf-8">
<title>Bayfield Capital Works – Business Card</title>
<link rel="stylesheet" href="https://fonts.googleapis.com/css2?family=Montserrat:wght@400;500;600;700&display=swap">
<style>
  :root {
    --navy: #1b3868;
    --green: #86c440;
    --paper: #f3f3f3;
    --ink: #2a2a2a;
    --backdrop: #1c1c1c;
    --white: #f5f5f5;
  }
  * { margin: 0; padding: 0; box-sizing: border-box; }
  html, body {
    width: 1200px; height: 1059px; overflow: hidden;
    background: var(--backdrop);
    font-family: "Montserrat", Arial, sans-serif;
  }
  .card {
    position: absolute; left: 256px; width: 688px; height: 392px;
    border-radius: 16px; overflow: hidden;
  }
  .card--front { top: 89px; background: var(--paper); }
  .card--back { top: 547px; background: var(--navy); }

  .brand { position: absolute; left: 0; right: 0; text-align: center; }
  .brand__square {
    position: absolute; left: 50%; transform: translateX(-50%);
    background: var(--green);
  }
  .card--front .brand__square { top: 48px; width: 64px; height: 64px; }
  .card--back .brand__square { top: 118px; width: 96px; height: 96px; }
  .brand__name {
    position: absolute; left: 0; right: 0;
    font-weight: 700; text-transform: uppercase; letter-spacing: 0.3px;
  }
  .card--front .brand__name { top: 145px; font-size: 17.5px; color: var(--navy); }
  .card--back .brand__name { top: 246px; font-size: 27px; color: var(--white); }
  .brand__tagline {
    position: absolute; left: 0; right: 0;
    font-weight: 600; text-transform: uppercase; color: var(--green);
  }
  .card--front .brand__tagline { top: 168px; font-size: 9.5px; letter-spacing: 1.3px; }
  .card--back .brand__tagline { top: 280px; font-size: 14px; letter-spacing: 1.8px; }

  .person { position: absolute; right: 380px; top: 232px; text-align: right; }
  .person__name {
    font-size: 27px; font-weight: 600; text-transform: uppercase;
    color: var(--navy); white-space: nowrap; line-height: 1;
  }
  .person__name .surname { color: var(--green); }
  .person__title { margin-top: 8px; font-size: 15.5px; color: var(--ink); }

  .divider {
    position: absolute; left: 330px; top: 214px; width: 1.5px; height: 89px;
    background: var(--navy);
  }

  .contacts { position: absolute; left: 352px; top: 208px; list-style: none; }
  .contacts li {
    display: flex; align-items: center; height: 26px;
    font-size: 14px; color: var(--ink); white-space: nowrap;
  }
  .contacts svg { width: 12px; height: 12px; margin-right: 10px; fill: var(--green); flex: none; }

  .address {
    position: absolute; left: 0; right: 0; top: 337px; text-align: center;
    font-size: 15.5px; color: var(--ink);
  }
</style>
</head>
<body>
  <section class="card card--front">
    <div class="brand">
      <span class="brand__square"></span>
      <div class="brand__name">Bayfield Capital Works, Inc</div>
      <div class="brand__tagline">Steady guidance to buy or sell a local business</div>
    </div>

    <div class="person">
      <div class="person__name">Glen R. <span class="surname">Harlow</span></div>
      <div class="person__title">Small Business Advisor</div>
    </div>

    <div class="divider"></div>

    <ul class="contacts">
      <li><svg viewBox="0 0 12 12"><path d="M1 4.5C1 3 3 2 6 2s5 1 5 2.5V5.5H8.5V4.3c-1.6-.5-3.4-.5-5 0V5.5H1z M2.5 6.5h7l1 4h-9z"/></svg>(555) 806-2147</li>
      <li><svg viewBox="0 0 12 12"><path d="M3.5 0.5h5a1 1 0 0 1 1 1v9a1 1 0 0 1-1 1h-5a1 1 0 0 1-1-1v-9a1 1 0 0 1 1-1zM4 2v7h4V2zM6 9.6a.6.6 0 1 0 0 1.2a.6.6 0 1 0 0-1.2z"/></svg>(555) 274-3918</li>
      <li><svg viewBox="0 0 12 12"><path d="M6 1l5.5 4v6h-11V5zM1.8 5.6L6 8.5l4.2-2.9L6 2.7z"/></svg>g.harlow@bayfieldcapitalworks.example</li>
      <li><svg viewBox="0 0 12 12"><circle cx="6" cy="6" r="5.5"/></svg>www.bayfieldcapitalworks.example</li>
    </ul>

    <div class="address">P.O. Box 418 Harbor Street Bayfield, WI 54814</div>
  </section>

  <section class="card card--back">
    <div class="brand">
      <span class="brand__square"></span>
      <div class="brand__name">Bayfield Capital Works, Inc</div>
      <div class="brand__tagline">Steady guidance to buy or sell a local business</div>
    </div>
  </section>
</body>
</html>
```